Lotstallmart.com Webpage Design

Design Brief for lotstallmart.com (Copy of Brief also in attached Word file)

Name of Website- lotstallmart.com (existing logo and look & feel of website to be changed)

Logo - Finalised. The logo files are attached with the brief as “logo.jpeg”. The “Blue- Grey” version of the logo is for use on lighter backgrounds and the “Orange-White” version of the logo is for use on darker backgrounds. (A full Black version of the logo is also attached). Both versions may be used in different parts of the website. All attached files are in .png format.
Status - The website in functional and is undergoing user trials. However, we want to improve the look & feel of the website so at it seems
a. cotemporary,
b. Easy to Navigate
c. professional and
d. Vibrant.

Please visit ‘lotstallmart.com’ to check out the website and its functionalities – please use it only as a reference for the features & functions to be provided, however the designer should use a ‘Free Hand’ in designing the composition of various parts of the webpage without getting too influenced by the existing design

Objective of the Website ‘lotstallmart.com –
a. It is a portal focussed on listing of ‘Retail’ specific real-estate properties by developers, owners and realty brokers. The properties shall listed under the following four categories-
i. Retail Malls
ii. Shopping Complexes
iii. High-street shops
iv. Retail Warehouses
*refer lotstallmart.com for better clarity

b. The abovementioned properties shall be listed either for ‘Sale’ or ‘rent\lease’ or both

c. Users shall visit the site in case they wish to acquire a retail \ shop space either on ‘sale’ or ‘rent’. These Users would be able to specify the ‘Search Criteria’ through the tool-bars provided on the website – the ‘Search Criteria’ shall comprise of ‘Type of space category’, ‘City’, ‘Locality’, transaction type ie ‘Rent \ Sale’ and ‘Area Range’

d. The main revenue model for the website shall be listing fee ( or advertising charges ) payable by those listing their properties on the website.

Three Main Pages of Website (lotstallmart.com) that need to be designed -
a. Main Home Page (visit the web link - http://lotstallmart.com/ ) - The main home page has the “Search Toolbar” for specifying of Search Criteria by the User. It shall also have the following features & functions-
i. Main Advertising Banner
ii. Featured Projects
iii. New Launches
iv. Toolbar with buttons – ‘Advertise with Us’, ‘Listings Alert’, ‘Mart Wizards’, ‘Advertiser Login’

b. Property Listings Page (visit the web link - http://lotstallmart.com/gurgaon-in-india ) - The List of property options that match the Criteria specified by the ‘User’ get displayed on this page.

c. Property Detail Page - When the ‘User’ clicks on the “More….” Button on the ‘Property Listings Page’ (given in point b. above) the web page with the details of the property opens. (For Example – visit the web link - http://lotstallmart.com/vorne-Shopping-Complex-vorne-quadrion-gurgaon-636 )

Note:- Please refer to attached ‘Shopping’ related images the designer may use them on the website to provide a look & feel of retail if required – either separately or rotate in a single window

Target Market(s)

Retailers & Investors looking for retail space, Real Estate Brokers, Developers

Industry/Entity Type

Advertising

Number of Pages Required

3 page

Requirements
Must have
• Refer to existing site lotstallmart.com -- all the existing functionalities are a must have.
Nice to have
• The Designer may use the retail related images on the website if required for making it more vibrant. Refer attached images Shopping(1-6).jpg

```html
<!DOCTYPE html>
<html lang="en">
<head>
<meta charset="utf-8">
<title>Lotstallmart.com – India's Leading Portal for Retail Space</title>
<link href="https://fonts.googleapis.com/css2?family=Roboto+Condensed:wght@400;700&family=Open+Sans:wght@400;600;700&display=swap" rel="stylesheet">
<style>
:root{
  --blue:#1e8fe8;
  --blue-dark:#1477c8;
  --ink:#333;
  --muted:#666;
  --nav:#1d1d1d;
  --panel:#dcdcdc;
  --card:#fff;
  --footer:#2b2b2b;
  --footer-text:#bdbdbd;
  --line:#d6d6d6;
}
*{box-sizing:border-box;margin:0;padding:0}
html,body{width:1200px;height:2624px;overflow:hidden}
body{background:#fff;font-family:"Open Sans",Arial,sans-serif;color:var(--ink);font-size:12px;position:relative}
.wrap{width:1000px;margin:0 auto;position:relative}
a{color:inherit;text-decoration:none}

/* top bar */
.topbar{height:30px;background:var(--blue);color:#fff;font-size:10.5px;display:flex;align-items:center;justify-content:space-between;padding:0 10px}
.lang{background:var(--blue-dark);padding:3px 10px;border-radius:2px}

/* header */
.header{height:100px;display:flex;align-items:center;justify-content:space-between}
.welcome{font-size:10.5px;color:#444}
.welcome span{margin:0 10px;color:#999}
.brand{display:flex;flex-direction:column;align-items:center;margin-left:90px}
.brand-row{display:flex;align-items:center;gap:8px}
.brand-mark{width:30px;height:30px;border-radius:50%;background:var(--blue)}
.brand-name{font-family:"Open Sans",sans-serif;font-weight:700;font-size:30px;color:#3a3a3a;letter-spacing:-.5px}
.brand-tag{font-size:8px;font-weight:700;color:#777;letter-spacing:.5px;margin-top:2px}
.btn{display:inline-block;background:var(--blue);color:#fff;font-weight:600;border-radius:2px;text-align:center;box-shadow:0 2px 3px rgba(0,0,0,.25)}
.login{padding:9px 20px;font-size:12px}

/* nav */
.nav{height:36px;background:var(--nav);display:flex;align-items:center;border-bottom:2px solid #000}
.nav .home{width:40px;height:36px;background:var(--blue);display:flex;align-items:center;justify-content:center}
.nav .item{color:#fff;font-family:"Roboto Condensed",sans-serif;font-size:14px;padding:0 30px;height:36px;line-height:36px;border-right:1px solid #3a3a3a}
.nav .item:first-of-type{padding:0 38px}
.nav .search{margin-left:auto;margin-right:10px;width:205px;height:22px;background:#2f2f2f;border:1px solid #444;position:relative}
.nav .search svg{position:absolute;right:6px;top:4px}

/* hero */
.hero{margin-top:22px;height:516px;position:relative;box-shadow:0 10px 18px -8px rgba(0,0,0,.45)}
.hero-photo{position:absolute;inset:0;background:
 radial-gradient(ellipse at 30% 50%,#e66a9a 0,rgba(230,106,154,0) 22%),
 linear-gradient(90deg,#a8762f 0%,#e2b26a 30%,#f0d08a 50%,#c58740 75%,#7a4a22 100%)}
.finder{position:absolute;left:642px;top:28px;width:305px;height:462px;background:rgba(28,28,28,.88);padding:22px 26px;color:#fff}
.finder h2{font-family:"Roboto Condensed",sans-serif;font-weight:700;font-size:25px;text-align:center;margin-bottom:14px}
.checks{display:grid;grid-template-columns:1fr 1fr;gap:12px 6px;font-size:10.5px;padding-left:8px;margin-bottom:18px}
.checks label{display:flex;align-items:center;gap:8px}
.checks i{width:9px;height:9px;background:#fff;display:inline-block}
.field{margin-bottom:12px}
.field p{font-size:10.5px;margin-bottom:6px}
.select{height:32px;background:#fff;color:#555;font-size:10.5px;display:flex;align-items:center;padding-left:10px;position:relative}
.select b{position:absolute;right:0;top:0;width:32px;height:32px;background:var(--blue);display:flex;align-items:center;justify-content:center}
.finder .go{display:block;width:115px;margin:18px auto 0;padding:9px 0;font-size:10.5px;font-weight:700}
.dots{position:absolute;bottom:10px;left:476px;display:flex;gap:8px}
.dots i{width:9px;height:9px;border-radius:50%;background:#fff;display:block}
.dots i.on{background:var(--blue)}

/* categories */
.cats{margin-top:23px;display:flex;justify-content:space-between}
.cat{width:231px;height:214px;position:relative;box-shadow:0 10px 14px -8px rgba(0,0,0,.45)}
.cat .ph{position:absolute;inset:0}
.cat .cap{position:absolute;left:0;right:0;bottom:0;height:80px;background:linear-gradient(rgba(0,0,0,0),rgba(0,0,0,.75) 35%);padding:22px 16px 0}
.cat h3{font-family:"Roboto Condensed",sans-serif;font-weight:700;color:var(--blue);font-size:21px}
.cat p{color:#fff;font-size:10.5px;line-height:1.6}

/* listings */
.block{margin-top:38px;display:flex;justify-content:space-between;position:relative}
.side{width:226px;height:385px;background:var(--panel);padding:14px 16px;box-shadow:0 10px 14px -8px rgba(0,0,0,.45);text-align:left}
.side h3{text-align:center;font-family:"Roboto Condensed",sans-serif;font-weight:700;font-size:22px;color:var(--blue);margin-bottom:12px}
.side .slider{display:flex;align-items:center;justify-content:space-between}
.side .slider .ph{width:150px;height:118px}
.main{width:742px}
.main-head{height:28px;display:flex;align-items:center;margin-bottom:16px}
.main-head h2{font-family:"Roboto Condensed",sans-serif;font-weight:700;font-size:23px;color:var(--blue)}
.main-head small{font-size:9px;color:#444;margin:6px 0 0 4px}
.main-head .rule{flex:1;height:1px;background:var(--line);margin:4px 14px 0}
.cards{display:flex;justify-content:space-between}
.card{width:236px;height:345px;background:var(--card);padding:16px 16px;box-shadow:0 0 6px rgba(0,0,0,.12),0 10px 14px -8px rgba(0,0,0,.4)}
.card .ph{width:200px;height:130px}
.city{font-family:"Roboto Condensed",sans-serif;font-weight:700;font-size:22px;color:var(--blue);margin:20px 0 6px}
.addr{display:flex;gap:12px;align-items:flex-start;font-size:11px;line-height:1.6;color:#333}
.addr svg{flex:none;margin-top:2px}
.kind{color:var(--blue);font-size:10.5px;margin:2px 0 12px}
.more{padding:8px 0;width:104px;font-size:11px}
.side .city{margin-top:38px}

/* info boxes */
.boxes{margin-top:45px;display:flex;justify-content:space-between}
.box{width:311px;height:316px;border:1px solid #ddd;padding:20px 22px;box-shadow:0 10px 14px -8px rgba(0,0,0,.35);position:relative}
.box h3{font-family:"Roboto Condensed",sans-serif;font-weight:700;font-size:19px;color:#222;margin-bottom:14px}
.box p{font-size:10.5px;line-height:1.75;color:#444}
.input{height:32px;border:1px solid #ccc;font-size:10px;color:#aaa;display:flex;align-items:center;padding-left:12px;margin:12px 0;width:244px}
.input.tall{height:62px;align-items:flex-start;padding-top:8px}
.box .act{position:absolute;left:20px;bottom:20px;width:100px;padding:8px 0;font-size:11px}
.box .lbl{font-size:10.5px;color:#333;margin-top:-4px}

/* footer */
.footer{position:absolute;left:0;right:0;top:2219px;bottom:0;background:var(--footer);color:var(--footer-text)}
.footer .wrap{height:100%}
.f-brand{position:absolute;left:0;top:44px;display:flex;flex-direction:column}
.f-brand .brand-name{color:#fff;font-size:30px}
.f-brand .brand-tag{color:#ccc;align-self:flex-start;margin-left:40px}
.f-about{position:absolute;left:0;top:130px;width:320px;font-size:10.5px;line-height:1.75}
.f-col{position:absolute;top:56px}
.f-col h4{font-family:"Roboto Condensed",sans-serif;font-weight:700;color:#fff;font-size:19px;margin-bottom:18px}
.ticks{display:grid;grid-template-columns:155px 150px;row-gap:12px;font-size:10.5px;color:#eee}
.ticks span{display:flex;align-items:center;gap:12px}
.contact{font-size:10.5px;line-height:1.75;color:#eee}
.contact .ln{display:flex;align-items:center;gap:8px}
.f-bottom{position:absolute;left:0;right:0;top:333px;display:flex;justify-content:space-between;font-size:10.5px;color:#eee}
.f-bottom span{margin:0 4px}
.social{position:absolute;left:0;top:363px;display:flex;gap:5px}
.social i{width:24px;height:24px;border:1.5px solid #bbb;border-radius:50%;display:block}
</style>
</head>
<body>

<div class="wrap">
  <div class="topbar">
    <span>Bangalore | Chennai | Greater Noida | Gurgaon | Hyderabad | Jaipur | Khanna | Kolkatta | Mumbai | Noida | Pune | Surat</span>
    <span class="lang">English &#9662;</span>
  </div>

  <header class="header">
    <div class="welcome">Welcome <span>|</span> &#9823; New Advertiser - Register</div>
    <div class="brand">
      <div class="brand-row"><i class="brand-mark"></i><span class="brand-name">lotstallmart</span></div>
      <div class="brand-tag">INDIA'S LEADING PORTAL FOR RETAIL SPACE</div>
    </div>
    <a class="btn login">Advertiser Login</a>
  </header>

  <nav class="nav">
    <a class="home"><svg width="18" height="16" viewBox="0 0 18 16"><path d="M9 1 1 8h2.5v7h4v-5h3v5h4V8H17z" fill="#fff"/></svg></a>
    <a class="item">Advertise with us</a>
    <a class="item">Mart Wizards</a>
    <a class="item">Listing Alert</a>
    <a class="item">Register</a>
    <div class="search"><svg width="12" height="12" viewBox="0 0 12 12"><circle cx="5" cy="5" r="3.5" stroke="#aaa" stroke-width="1.5" fill="none"/><path d="m7.5 7.5 3 3" stroke="#aaa" stroke-width="1.5"/></svg></div>
  </nav>

  <section class="hero">
    <div class="hero-photo" role="img" aria-label="Shopper carrying colourful bags inside a bright mall"></div>
    <form class="finder">
      <h2>SELECT RETAIL FORMAT</h2>
      <div class="checks">
        <label><i></i>Retail Malls</label>
        <label><i></i>Shopping Complex</label>
        <label><i></i>High Street Shops</label>
        <label><i></i>Retail Warehouses</label>
      </div>
      <div class="field"><p>Sale Or Rent Or Both:</p><div class="select">Both<b><svg width="10" height="6"><path d="M0 0h10L5 6z" fill="#fff"/></svg></b></div></div>
      <div class="field"><p>Select City:</p><div class="select">-Select-<b><svg width="10" height="6"><path d="M0 0h10L5 6z" fill="#fff"/></svg></b></div></div>
      <div class="field"><p>Select Locality/Micro-Market</p><div class="select">-Select-<b><svg width="10" height="6"><path d="M0 0h10L5 6z" fill="#fff"/></svg></b></div></div>
      <div class="field"><p>Enter Keywords:</p><div class="select">Name of Project,Devaloper etc<b><svg width="10" height="6"><path d="M0 0h10L5 6z" fill="#fff"/></svg></b></div></div>
      <a class="btn go">SEARCH</a>
    </form>
    <div class="dots"><i></i><i class="on"></i><i></i></div>
  </section>

  <section class="cats">
    <div class="cat"><div class="ph" role="img" aria-label="Family shopping in a mall" style="background:linear-gradient(135deg,#c9a47a,#8c6a4c)"></div><div class="cap"><h3>Retail Malls</h3><p>Lorem Ipsum is simply dummy text<br>of the printing and typesetting</p></div></div>
    <div class="cat"><div class="ph" role="img" aria-label="Shopper with bags in a shopping complex" style="background:linear-gradient(135deg,#f2d38a,#c98c3c)"></div><div class="cap"><h3>Shopping Complex</h3><p>Lorem Ipsum is simply dummy text<br>of the printing and typesetting</p></div></div>
    <div class="cat"><div class="ph" role="img" aria-label="Shopper on a high street" style="background:linear-gradient(135deg,#6a6a6a,#2e2e2e)"></div><div class="cap"><h3>High Street Shops</h3><p>Lorem Ipsum is simply dummy text<br>of the printing and typesetting</p></div></div>
    <div class="cat"><div class="ph" role="img" aria-label="Group of shoppers at a sale" style="background:linear-gradient(135deg,#b85a3a,#6c4a3c)"></div><div class="cap"><h3>Retail Warehouses</h3><p>Lorem Ipsum is simply dummy text<br>of the printing and typesetting</p></div></div>
  </section>

  <section class="block">
    <aside class="side">
      <h3>Specials</h3>
      <div class="slider">
        <svg width="12" height="16"><path d="M10 1 2 8l8 7" stroke="#222" stroke-width="3" fill="none"/></svg>
        <div class="ph" role="img" aria-label="Red and white retail building" style="background:linear-gradient(#9cc3e6,#c44 60%,#ddd)"></div>
        <svg width="12" height="16"><path d="m2 1 8 7-8 7" stroke="#222" stroke-width="3" fill="none"/></svg>
      </div>
      <div class="city">Chennai</div>
      <div class="addr"><svg width="22" height="30" viewBox="0 0 22 30"><path d="M11 0a11 11 0 0 0-11 11c0 8 11 19 11 19s11-11 11-19A11 11 0 0 0 11 0z" fill="#444"/><circle cx="11" cy="11" r="4" fill="#dcdcdc"/></svg><div>The Meridian Mall<br>Tamil Nadu,Chennai<br>Velacheri -600042</div></div>
      <div class="kind">Retail Malls</div>
      <a class="btn more">View More</a>
    </aside>
    <div class="main">
      <div class="main-head"><h2>Featured Retail Projects</h2><small>Across India</small><span class="rule"></span><svg width="28" height="16"><path d="M10 1 3 8l7 7M18 1l7 7-7 7" stroke="#111" stroke-width="3" fill="none"/></svg></div>
      <div class="cards">
        <div class="card"><div class="ph" role="img" aria-label="Tall hotel and retail towers at dusk" style="background:linear-gradient(#7aa4cc,#3c4a5c)"></div><div class="city">Faridabad</div><div class="addr"><svg width="22" height="30" viewBox="0 0 22 30"><path d="M11 0a11 11 0 0 0-11 11c0 8 11 19 11 19s11-11 11-19A11 11 0 0 0 11 0z" fill="#444"/><circle cx="11" cy="11" r="4" fill="#fff"/></svg><div>Orin 81 High Street<br>Haryana,&nbsp; Faridabad<br>Sector-81 -600042</div></div><div class="kind">Retail Malls</div><a class="btn more">View More</a></div>
        <div class="card"><div class="ph" role="img" aria-label="Lit tower at night" style="background:linear-gradient(#1b2340,#6a4a3a)"></div><div class="city">Thiruvananthapuram</div><div class="addr"><svg width="22" height="30" viewBox="0 0 22 30"><path d="M11 0a11 11 0 0 0-11 11c0 8 11 19 11 19s11-11 11-19A11 11 0 0 0 11 0z" fill="#444"/><circle cx="11" cy="11" r="4" fill="#fff"/></svg><div>The Meridian Mall<br>Tamil Nadu,Chennai<br>Velacheri -600042</div></div><div class="kind">Retail Malls</div><a class="btn more">View More</a></div>
        <div class="card"><div class="ph" role="img" aria-label="Busy mall atrium" style="background:linear-gradient(#d8b488,#7a5a40)"></div><div class="city">Bangalore</div><div class="addr"><svg width="22" height="30" viewBox="0 0 22 30"><path d="M11 0a11 11 0 0 0-11 11c0 8 11 19 11 19s11-11 11-19A11 11 0 0 0 11 0z" fill="#444"/><circle cx="11" cy="11" r="4" fill="#fff"/></svg><div>The Meridian Mall<br>Tamil Nadu,Chennai<br>Velacheri -600042</div></div><div class="kind">Retail Malls</div><a class="btn more">View More</a></div>
      </div>
    </div>
  </section>

  <section class="block" style="margin-top:53px">
    <aside class="side">
      <div class="ph" role="img" aria-label="Modern mall building under blue sky" style="width:192px;height:172px;margin:4px auto 0;background:linear-gradient(#6a9ed0,#8a8a8a 60%,#555)"></div>
      <div class="city" style="margin-top:22px">New Delhi</div>
      <div class="addr"><svg width="22" height="30" viewBox="0 0 22 30"><path d="M11 0a11 11 0 0 0-11 11c0 8 11 19 11 19s11-11 11-19A11 11 0 0 0 11 0z" fill="#444"/><circle cx="11" cy="11" r="4" fill="#dcdcdc"/></svg><div>The Meridian Mall<br>Tamil Nadu,Chennai<br>Velacheri -600042</div></div>
      <div class="kind">Retail Malls</div>
      <a class="btn more">View More</a>
    </aside>
    <div class="main">
      <div class="main-head"><h2>Featured New Launches</h2><small>Across India</small><span class="rule"></span><svg width="28" height="16"><path d="M10 1 3 8l7 7M18 1l7 7-7 7" stroke="#111" stroke-width="3" fill="none"/></svg></div>
      <div class="cards">
        <div class="card"><div class="ph" role="img" aria-label="Mall entrance with orange facade" style="background:linear-gradient(#c86a30,#6a4a3a)"></div><div class="city">Chennai</div><div class="addr"><svg width="22" height="30" viewBox="0 0 22 30"><path d="M11 0a11 11 0 0 0-11 11c0 8 11 19 11 19s11-11 11-19A11 11 0 0 0 11 0z" fill="#444"/><circle cx="11" cy="11" r="4" fill="#fff"/></svg><div>The Meridian Mall<br>Tamil Nadu,Chennai<br>Velacheri -600042</div></div><div class="kind">Retail Malls</div><a class="btn more">View More</a></div>
        <div class="card"><div class="ph" role="img" aria-label="Glass mall frontage" style="background:linear-gradient(#9aa4b0,#3a3e48)"></div><div class="city">Bangalore</div><div class="addr"><svg width="22" height="30" viewBox="0 0 22 30"><path d="M11 0a11 11 0 0 0-11 11c0 8 11 19 11 19s11-11 11-19A11 11 0 0 0 11 0z" fill="#444"/><circle cx="11" cy="11" r="4" fill="#fff"/></svg><div>The Meridian Mall<br>Tamil Nadu,Chennai<br>Velacheri -600042</div></div><div class="kind">Retail Malls</div><a class="btn more">View More</a></div>
        <div class="card"><div class="ph" role="img" aria-label="Illuminated tower against blue evening sky" style="background:linear-gradient(#2a4a90,#c09a50)"></div><div class="city">Gurgaon</div><div class="addr"><svg width="22" height="30" viewBox="0 0 22 30"><path d="M11 0a11 11 0 0 0-11 11c0 8 11 19 11 19s11-11 11-19A11 11 0 0 0 11 0z" fill="#444"/><circle cx="11" cy="11" r="4" fill="#fff"/></svg><div>The Meridian Mall<br>Tamil Nadu,Chennai<br>Velacheri -600042</div></div><div class="kind">Retail Malls</div><a class="btn more">View More</a></div>
      </div>
    </div>
  </section>

  <section class="boxes">
    <div class="box">
      <h3>LISTING ALERT !</h3>
      <p>Suscribe&nbsp; for Fortnightly Email update on New Listings @ LotStallMart</p>
      <div class="input">Enter your email address</div>
      <div class="input">Select option</div>
      <p class="lbl">Select retail format of interest</p>
      <div class="input">Select cities of interest</div>
      <a class="btn act">Subcribe</a>
    </div>
    <div class="box">
      <h3>EDITOR'S CHOICE !</h3>
      <p>Veltra Group launched its largest mall in NCR inspired by classical Roman-style architecture. Situated at Indirapuram with 4.5 lakh sq. ft of total area, Veltra Mall commits to offer a unique shopping experience with over 100 national &amp; international brands and entertainment. The mall has been designed as a one-stop-destination for entertainment and leisure.</p>
      <a class="btn act">More</a>
    </div>
    <div class="box">
      <h3>MART WIZARDS !</h3>
      <p>Post your Retail Space requirement with us and our experts shall get back with suitable options</p>
      <div class="input">Enter your email address</div>
      <div class="input">Mobile</div>
      <div class="input tall">Add Description of Requirement</div>
      <a class="btn act">Send</a>
    </div>
  </section>
</div>

<footer class="footer">
  <div class="wrap">
    <div class="f-brand">
      <div class="brand-row"><i class="brand-mark"></i><span class="brand-name">lotstallmart</span></div>
      <div class="brand-tag">INDIA'S LEADING PORTAL FOR RETAIL SPACE</div>
    </div>
    <p class="f-about">Lotstallmart.com - About Us Lotstallmart.com is a Specialised Web based platform for Retail Space, featuring properties across India under various formats such as Retail Malls, Shopping Complexes, High-street Shops. Also featured are Retail Warehouses which provide the logistic back-end for the retail business. Lotstallmart.com is useful to various category of users as follows- a. Devel More...</p>

    <div class="f-col" style="left:370px">
      <h4>ABOUT STALLHAVEN REALTY</h4>
      <div class="ticks">
        <span><svg width="10" height="9"><path d="m1 5 3 3 5-7" stroke="#ddd" stroke-width="2" fill="none"/></svg>About Us</span>
        <span><svg width="10" height="9"><path d="m1 5 3 3 5-7" stroke="#ddd" stroke-width="2" fill="none"/></svg>Retail Malls</span>
        <span><svg width="10" height="9"><path d="m1 5 3 3 5-7" stroke="#ddd" stroke-width="2" fill="none"/></svg>Privacy Policy</span>
        <span><svg width="10" height="9"><path d="m1 5 3 3 5-7" stroke="#ddd" stroke-width="2" fill="none"/></svg>Shopping Complex</span>
        <span><svg width="10" height="9"><path d="m1 5 3 3 5-7" stroke="#ddd" stroke-width="2" fill="none"/></svg>Terms of Use</span>
        <span><svg width="10" height="9"><path d="m1 5 3 3 5-7" stroke="#ddd" stroke-width="2" fill="none"/></svg>High Street Shops</span>
        <span><svg width="10" height="9"><path d="m1 5 3 3 5-7" stroke="#ddd" stroke-width="2" fill="none"/></svg>Contact Us</span>
        <span><svg width="10" height="9"><path d="m1 5 3 3 5-7" stroke="#ddd" stroke-width="2" fill="none"/></svg>Retail Warehouses</span>
        <span><svg width="10" height="9"><path d="m1 5 3 3 5-7" stroke="#ddd" stroke-width="2" fill="none"/></svg>Site Map</span>
      </div>
    </div>

    <div class="f-col contact" style="left:722px">
      <h4>ABOUT STALLHAVEN REALTY</h4>
      <p>Stallhaven Realty<br>Suite 219, 2nd Floor,<br>Lorem Ipsum is simply,<br>Sector-y, Noida - 201309</p>
      <p class="ln" style="margin-top:12px"><svg width="11" height="11" viewBox="0 0 11 11"><path d="M2 0h2l1 3-1.5 1a6 6 0 0 0 3.5 3.5L8 6l3 1v2a2 2 0 0 1-2 2A9 9 0 0 1 0 2a2 2 0 0 1 2-2z" fill="#ddd"/></svg>Phone : 000-000-0000</p>
      <p class="ln"><svg width="12" height="10" viewBox="0 0 12 10"><rect x="0" y="3" width="12" height="6" fill="#ddd"/><rect x="3" y="0" width="6" height="3" fill="#ddd"/></svg>Fax : 000 - 000 - 0000</p>
    </div>

    <div class="f-bottom">
      <div>Privacy Policy <span>|</span> Store Locator <span>|</span> Advanced Search <span>|</span> Terms &amp; Conditions</div>
      <div>&copy; Lotstallmart Decor 2014- All rights reserved</div>
    </div>
    <div class="social"><i></i><i></i><i></i><i></i><i></i></div>
  </div>
</footer>

</body>
</html>
```